Business Card Design Project

Doctor, Pain Management. Need a new business card design with appointment info on the back. New address is 18 Corvell Road, Suite 304, Brisdale, NJ 07391. Right now I believe the rest of the information is staying the same.

```html
<!DOCTYPE html>
<html lang="en">
<head>
<meta charset="utf-8">
<title>Steady Relief Pain Care – Business Card</title>
<link href="https://fonts.googleapis.com/css2?family=Gelasio:ital,wght@0,400;0,700;1,700&display=swap" rel="stylesheet">
<style>
  :root {
    --backdrop: #3a3a3a;
    --card: #262626;
    --card-edge: #1c1c1c;
    --ink: #f2f2f2;
    --accent: #f4e63c;
    --accent-soft: #d8d21a;
    --rule: #e6e6e6;
  }
  * { box-sizing: border-box; margin: 0; padding: 0; }
  html, body { width: 1200px; height: 717px; overflow: hidden; }
  body {
    background: var(--backdrop);
    font-family: "Gelasio", Georgia, serif;
    color: var(--ink);
    position: relative;
  }
  .card {
    position: absolute;
    top: 204px;
    width: 540px;
    height: 309px;
    background: var(--card);
    border-radius: 12px;
    box-shadow: 0 0 0 1px var(--card-edge);
    overflow: hidden;
  }
  .card--front { left: 40px; text-align: center; }
  .card--back { left: 620px; }

  /* front */
  .front-figure {
    position: absolute;
    left: 190px; top: 70px;
    width: 160px; height: 200px;
    border-radius: 50% 50% 40% 40%;
    background: radial-gradient(ellipse at center, rgba(120,60,40,.35), rgba(38,38,38,0) 70%);
  }
  .practice-name {
    position: relative;
    margin-top: 30px;
    font-size: 36px;
    font-weight: 700;
    font-style: italic;
    color: var(--accent);
  }
  .doctor-name {
    position: relative;
    margin-top: 22px;
    font-size: 22px;
    font-weight: 700;
  }
  .credentials {
    position: relative;
    font-size: 14px;
    color: var(--accent-soft);
    margin-bottom: 10px;
  }
  .contact-line {
    position: relative;
    font-size: 19px;
    line-height: 1.3;
  }

  /* back */
  .appt-title {
    position: absolute;
    left: 230px; top: 22px;
    width: 280px;
    text-align: center;
    font-size: 30px;
  }
  .appt-note {
    position: absolute;
    left: 210px; top: 70px;
    width: 320px;
    text-align: center;
    font-size: 17px;
    line-height: 1.2;
  }
  .field {
    position: absolute;
    font-size: 18px;
    display: flex;
    align-items: flex-end;
    gap: 6px;
  }
  .field .blank { border-bottom: 1.5px solid var(--rule); height: 1px; margin-bottom: 5px; }
  .field--for { left: 28px; top: 118px; }
  .field--for .blank { width: 470px; }
  .field--date { left: 28px; top: 148px; }
  .field--date .blank { width: 200px; }
  .field--time { left: 300px; top: 148px; }
  .field--time .blank { width: 160px; }
  .weekdays {
    position: absolute;
    left: 28px; top: 188px;
    display: flex;
    gap: 16px;
    font-size: 20px;
  }
  .day { display: flex; align-items: center; gap: 5px; }
  .day::before {
    content: "";
    width: 16px; height: 16px;
    background: var(--ink);
    display: inline-block;
  }
  .back-phones {
    position: absolute;
    left: 28px; bottom: 30px;
    font-size: 16px;
    line-height: 1.2;
    color: var(--accent-soft);
  }
  .back-web {
    position: absolute;
    right: 28px; bottom: 26px;
    text-align: right;
    font-size: 18px;
    line-height: 1.25;
    color: var(--accent-soft);
  }
</style>
</head>
<body>
  <section class="card card--front">
    <div class="front-figure" role="img" aria-label="Faint illustration of a human body outline highlighting areas of pain"></div>
    <h1 class="practice-name">Steady Relief Pain Care</h1>
    <p class="doctor-name">Dr. Lianwei Tsao</p>
    <p class="credentials">M.D., Ph.D.</p>
    <p class="contact-line">(973) 555-0148</p>
    <p class="contact-line">(973) 555.0162</p>
    <p class="contact-line">www.steadyreliefpc.com</p>
    <p class="contact-line">steadyrelief.office@mail.com</p>
    <p class="contact-line">18 Corvell Road, Suite 304, Brisdale, NJ 07391</p>
  </section>

  <section class="card card--back">
    <h2 class="appt-title">Appoinment</h2>
    <p class="appt-note">If you are unable to keep your appoinment, please contact us as soon as posible.</p>
    <div class="field field--for"><span>For:</span><span class="blank"></span></div>
    <div class="field field--date"><span>Date:</span><span class="blank"></span></div>
    <div class="field field--time"><span>Time:</span><span class="blank"></span></div>
    <div class="weekdays">
      <span class="day">Mon</span>
      <span class="day">Tue</span>
      <span class="day">Wed</span>
      <span class="day">Thu</span>
      <span class="day">Fri</span>
      <span class="day">Sat</span>
      <span class="day">Sun</span>
    </div>
    <div class="back-phones">
      <p>(973) 555-0148</p>
      <p>(973) 555.0162</p>
    </div>
    <div class="back-web">
      <p>www.steadyreliefpc.com</p>
      <p>steadyrelief.office@mail.com</p>
    </div>
  </section>
</body>
</html>
```